New Business Card for Web Design/Internet Marketing Company

Looking for a great looking new business card. We are a 10 year old web design, internet marketing and website management company that works mostly with small businesses.

Our new card needs to better match the colors and style of our website, be bold, extremely usable and slightly edgy.

Target Market(s)

Small/Medium businesses that have websites

Industry/Entity Type

Internet

Requirements
Must have
• Front and back design, full color, rounded corners please

Must use the colors/style of our website (JPG provided)

INFO FOR CARDS (as readable as possible please)
Mark Lenner
President/CEO
mark@trelvanmedia.example
Phone: 520-381-7459
Toll Free: 866-381-7459
Address: 4315 W. Calloway Ave. Ste. 140, Tucson, AZ 85792

THINGS I WANT TO PROMOTE (if there is room):
1. Our Website - www.trelvanmedia.example

2. Social Media
Twitter: @trelvanmedia
Facebook: www.facebook.com/trelvanmedia

3. Our Services
Web Design
Internet Marketing
Website Management

```html
<!DOCTYPE html>
<html lang="en">
<head>
<meta charset="utf-8">
<title>Trelvan Media – Business Card</title>
<link href="https://fonts.googleapis.com/css2?family=Source+Sans+3:wght@400;600;700&display=swap" rel="stylesheet">
<style>
  :root {
    --backdrop: #ece9e4;
    --card-white: #ffffff;
    --brand-blue: #0a8cc6;
    --band-gray: #5f5f5f;
    --back-gray: #616161;
    --text-dark: #4a4a4a;
    --text-light: #ffffff;
    --line-light: rgba(255,255,255,0.55);
  }
  * { margin: 0; padding: 0; box-sizing: border-box; }
  html, body {
    width: 1200px; height: 402px; overflow: hidden;
    background: var(--backdrop);
    font-family: "Source Sans 3", "Myriad Pro", sans-serif;
  }
  .canvas { position: relative; width: 1200px; height: 402px; }

  .card {
    position: absolute; top: 58px; height: 294px; overflow: hidden;
    border-radius: 3px;
    box-shadow: 0 2px 6px rgba(0,0,0,0.25);
  }

  /* Front */
  .card-front { left: 61px; width: 527px; background: var(--card-white); }
  .brand-name {
    position: absolute; top: 52px; left: 0; width: 100%; text-align: center;
    font-size: 54px; font-weight: 700; color: var(--brand-blue);
    letter-spacing: -0.5px; line-height: 60px;
  }
  .brand-tagline {
    position: absolute; top: 100px; right: 68px;
    font-size: 17px; font-weight: 400; color: var(--text-dark); line-height: 20px;
  }
  .name-band {
    position: absolute; top: 162px; left: 0; width: 100%; height: 23px;
    background: var(--band-gray); color: var(--text-light);
    text-align: center; line-height: 23px;
  }
  .name-band .person { font-size: 17px; font-weight: 700; }
  .name-band .role { font-size: 13px; font-weight: 400; }
  .contact-band {
    position: absolute; top: 189px; left: 0; width: 100%; bottom: 0;
    background: var(--brand-blue); color: var(--text-light);
    font-size: 13px;
  }
  .contact-left {
    position: absolute; right: 281px; top: 16px; text-align: right;
    line-height: 18px;
  }
  .contact-left .address { margin-top: 5px; line-height: 15px; }
  .social { display: flex; align-items: center; justify-content: flex-end; gap: 3px; }
  .social-mark { width: 9px; height: 9px; background: var(--text-light); opacity: 0.85; }
  .divider {
    position: absolute; left: 262px; top: 14px; bottom: 14px; width: 1px;
    background: var(--line-light);
  }
  .contact-right {
    position: absolute; left: 275px; top: 16px;
    line-height: 18.5px;
  }
  .contact-row { display: flex; align-items: center; gap: 5px; }
  .contact-row svg { width: 10px; height: 10px; flex: none; }

  /* Back */
  .card-back { left: 627px; width: 512px; background: var(--back-gray); color: var(--text-light); text-align: center; }
  .back-brand { position: absolute; top: 64px; width: 100%; font-size: 46px; font-weight: 700; line-height: 56px; }
  .services-title {
    position: absolute; top: 156px; left: 50%; transform: translateX(-50%);
    width: 172px; font-size: 22px; font-weight: 600; line-height: 24px; padding-bottom: 3px;
    border-bottom: 2px solid var(--text-light);
  }
  .services-list {
    position: absolute; top: 200px; width: 100%;
    font-size: 20px; font-weight: 400; line-height: 26px;
  }
</style>
</head>
<body>
<main class="canvas">

  <section class="card card-front" aria-label="Card front">
    <div class="brand-name">Trelvan Media</div>
    <div class="brand-tagline">Sites built to grow</div>

    <div class="name-band">
      <span class="person">Mark Lenner,</span> <span class="role">President/CEO</span>
    </div>

    <div class="contact-band">
      <div class="contact-left">
        <div class="social"><span class="social-mark"></span>trelvanmedia</div>
        <div class="social"><span class="social-mark"></span>@trelvanmedia</div>
        <div class="address">4315 W. Calloway Ave. Ste. 140<br>Tucson, AZ 85792</div>
      </div>
      <div class="divider"></div>
      <div class="contact-right">
        <div class="contact-row">
          <svg viewBox="0 0 10 10" aria-hidden="true"><circle cx="5" cy="5" r="4.5" fill="none" stroke="#fff"/><path d="M3 3.2l1 -.5 .8 1.4-.6.5a3 3 0 0 0 1.3 1.3l.5-.6 1.4.8-.5 1A4 4 0 0 1 3 3.2z" fill="#fff"/></svg>
          520-381-7459
        </div>
        <div class="contact-row">
          <svg viewBox="0 0 10 10" aria-hidden="true"><circle cx="5" cy="5" r="4.5" fill="none" stroke="#fff"/><path d="M3 3.2l1 -.5 .8 1.4-.6.5a3 3 0 0 0 1.3 1.3l.5-.6 1.4.8-.5 1A4 4 0 0 1 3 3.2z" fill="#fff"/></svg>
          866-381-7459
        </div>
        <div class="contact-row">
          <svg viewBox="0 0 10 10" aria-hidden="true"><rect x="0.5" y="2" width="9" height="6" fill="#fff"/><path d="M0.5 2l4.5 3.5 4.5-3.5" fill="none" stroke="#0a8cc6" stroke-width="0.8"/></svg>
          mark@trelvanmedia.example
        </div>
        <div class="contact-row">
          <svg viewBox="0 0 10 10" aria-hidden="true"><circle cx="5" cy="5" r="4.3" fill="none" stroke="#fff"/><ellipse cx="5" cy="5" rx="2" ry="4.3" fill="none" stroke="#fff" stroke-width="0.7"/><path d="M0.7 5h8.6" stroke="#fff" stroke-width="0.7"/></svg>
          www.trelvanmedia.example
        </div>
      </div>
    </div>
  </section>

  <section class="card card-back" aria-label="Card back">
    <div class="back-brand">Trelvan Media</div>
    <div class="services-title">Our Services</div>
    <div class="services-list">
      Web Design &nbsp;•&nbsp; Internet Marketing<br>
      Website Management
    </div>
  </section>

</main>
</body>
</html>
```